Im want a website LIKE VRX's and FleetHollow.com's with product payment options like Trenzo's

I need a website LIKE VRX with a header made EXACTLY LIKE THAT OF FLEETHOLLOWS .

The front page photo should be like that of FLEETHOLLOW's webpage as well.

The name of the website will be called "M.K. (Caldera Key)".

We will be targeting ALL MARKETS in a small town in central Panama and charging businesses "listing fees" like a phone book does but also providing informational blogs, news, and other interesting activities.

THIS IS A MULTI PAGE WEBSITE

THIS IS WHERE VRX's website meets Brivelle/FleetHollow.

Once the layout is built I will tweak and modify, add information, and upload items for sale.

Here is a list of specific categories that should be listed out above the front page header image/search bar

-- Home -- News -- Travel -- Activities -- Shop & Dine -- Store -- More... --

These categories should be spread across the bottom of the page in three sections:

WHATS SO GREAT ABOUT (Caldera Key),
HAND PICKED TOURS
ACTIVITIES etc.

Also lets use www.Trenzo.example 's
"HOT DESTINATIONS"
"BEAT THE BEST PRICES IN CALDERA"
"OCTOBERS INSIDER PICKS"
"TOP DESTINATIONS"
and spread them in four sections side-by-side near the bottom of the page.

Overall I would like to see the finished product to be something LIKE VRX's and FleetHollows.

WE NEED ONLINE PAYMENT OPTIONS LIKE BRIVELLE'S WEBSITE HAS

This will be a desktop website but should be very mobile friendly as well.

-rodmund

P.S. Good luck!

If it isn't already too late to change the website name, the name of the website should be "Caldera Key". Added Friday, October 9, 2015

What do you guys think the budget should be to win this? Added Saturday, October 10, 2015

www.palmorra.example is the most amazing simple site. Whoever can make me a replica with my specifications will win immediately!!!! Added Sunday, October 18, 2015

OMG www.palmorra.example is the bomb!So simple and elegant. Whoever can make me an EXACT REPLICA OF WWW.PALMORRA.EXAMPLE as my site with the specifications mentioned in my brief will take home the $825.00 immediately! Good luck amigos! Added Sunday, October 18, 2015

Does anybody know how to add recurring monthly billing options on this website? Added Sunday, October 18, 2015

ALL MARKETS

Product

Coded - Design and coding required

5+ page

• Coinvey payment options.
• I must be able to add and remove photos/text and video from the HTML files in the page.
• Be creative my friends, and may the odds be forever in your favor!
• I added some photos of a good layout for our page below.

```html
<!DOCTYPE html>
<html lang="en">
<head>
<meta charset="utf-8">
<title>Caldera Key</title>
<link href="https://fonts.googleapis.com/css2?family=Oswald:wght@400;500;600&family=Open+Sans:wght@400;600;700&display=swap" rel="stylesheet">
<style>
:root{
  --orange:#f07b2b;
  --blue:#1f78ad;
  --blue-dark:#17608c;
  --card-blue:#2a88c0;
  --ink:#333;
  --muted:#8a8a8a;
  --line:#e3e3e3;
  --topbar:#2f3337;
  --footer:#2b2d30;
  --footer-bottom:#202224;
  --white:#fff;
  --star:#f2b01e;
}
*{box-sizing:border-box;margin:0;padding:0}
html,body{width:1200px;height:2412px;overflow:hidden}
body{font-family:"Open Sans",Arial,sans-serif;color:var(--ink);background:var(--white);font-size:13px}
h1,h2,h3,h4{font-family:"Oswald",Arial,sans-serif;font-weight:500;text-transform:uppercase}
.container{width:1000px;margin:0 auto;position:relative}

/* top bar */
.topbar{height:36px;background:var(--topbar);color:#cfd3d6;font-size:11px}
.topbar .container{display:flex;justify-content:space-between;align-items:center;height:36px}
.topbar .opts span{margin-right:18px}
.topbar .account{display:flex;align-items:center;gap:6px}
.topbar .account i{width:9px;height:9px;border-radius:50%;background:#cfd3d6;display:inline-block}

/* header */
.site-header{height:84px;border-bottom:1px solid var(--line)}
.site-header .container{display:flex;justify-content:space-between;align-items:center;height:84px}
.logo{font-family:"Oswald",Arial,sans-serif;font-size:30px;font-weight:500;color:var(--orange);display:flex;align-items:center;gap:10px}
.logo i{width:14px;height:14px;background:var(--blue);display:inline-block}
.main-nav{display:flex;height:84px}
.main-nav a{display:flex;align-items:center;padding:0 20px;font-size:12px;font-weight:600;text-transform:uppercase;color:#555;text-decoration:none;border-left:1px solid var(--line)}
.main-nav a.active{color:var(--orange);border-top:3px solid var(--orange)}

/* hero */
.hero{position:relative;height:710px;overflow:hidden}
.hero-photo{position:absolute;inset:0;background:linear-gradient(180deg,#3e9fd8 0%,#8cccef 40%,#bfe6f2 58%,#4fc2c4 66%,#e9dcc0 80%,#d9c6a0 100%)}
.hero-copy{position:absolute;top:480px;left:0;right:0;text-align:center}
.hero-copy h1{font-size:40px;color:#fff;letter-spacing:1px;font-weight:500}
.hero-search{margin:22px auto 0;width:440px;height:40px;display:flex;background:#fff;border-radius:3px;overflow:hidden}
.hero-search span{flex:1;padding:0 14px;line-height:40px;font-size:11px;color:#aaa}
.hero-search b{width:90px;background:var(--blue);color:#fff;font-size:11px;line-height:40px;text-align:center;font-weight:600}
.hero-arrows{display:flex;justify-content:center;gap:6px;margin-top:18px}
.hero-arrows span{width:28px;height:24px;background:#fff;border-radius:3px;display:flex;align-items:center;justify-content:center}
.hero-curve{position:absolute;left:0;bottom:0}

/* welcome */
.welcome{height:130px;text-align:center;padding-top:14px}
.welcome h2{font-size:30px;color:#2d3a44}
.welcome p{width:760px;margin:10px auto 0;font-size:11px;line-height:17px;color:var(--muted)}

/* services */
.services{height:350px}
.services .container{display:flex;gap:30px;padding-top:20px}
.service{flex:1;background:#f4f4f4;border:1px solid var(--line);height:310px;text-align:center}
.service-head{height:70px;background:var(--card-blue);position:relative;display:flex;align-items:center;justify-content:center}
.service-head h3{color:#fff;font-size:20px;letter-spacing:.5px}
.service-icon{height:90px;display:flex;align-items:center;justify-content:center;padding-top:14px}
.service p{font-size:11px;line-height:16px;color:var(--muted);padding:10px 38px 0}
.btn{display:inline-block;background:var(--orange);color:#fff;font-size:10px;font-weight:700;text-transform:uppercase;padding:8px 18px;border-radius:2px}
.service .btn{margin-top:18px}

/* find holiday */
.find{height:250px;background:var(--blue-dark);color:#fff}
.find .container{padding-top:28px}
.find h2{font-size:26px}
.find p{font-size:11px;line-height:17px;color:#cfe2ee;width:640px;margin-top:10px}
.find-form{display:flex;gap:18px;margin-top:30px}
.find-form span{flex:1;height:40px;background:#fff;color:#666;font-size:11px;display:flex;align-items:center;justify-content:space-between;padding:0 12px;text-transform:uppercase;border-radius:2px}
.find-form span::after{content:"";border:5px solid transparent;border-top-color:#777;margin-top:5px}
.find-form .btn{flex:0 0 150px;height:40px;line-height:24px;text-align:center;font-size:11px}

/* packages */
.packages{height:510px;text-align:center}
.packages h2{font-size:30px;color:#2d3a44;padding-top:40px}
.package-list{display:flex;gap:22px;margin-top:36px;text-align:left}
.package{flex:1;border:1px solid var(--line);height:340px;background:#fff}
.package-photo{height:168px}
.package-body{padding:12px 14px}
.package h4{font-size:16px;color:#2d3a44}
.rating{display:flex;align-items:center;gap:6px;margin-top:6px;font-size:10px;color:var(--blue)}
.stars{color:var(--star);font-size:13px;letter-spacing:1px}
.package .place{font-size:10px;color:var(--muted);margin-top:4px}
.package-foot{display:flex;justify-content:space-between;align-items:flex-end;margin-top:14px}
.price small{display:block;font-size:10px;color:var(--muted)}
.price b{font-size:22px;color:#2d3a44;font-family:"Oswald",Arial,sans-serif;font-weight:500}

/* footer */
.site-footer{height:352px;background:var(--footer);color:#b9bcbf}
.site-footer .container{display:flex;padding-top:36px;height:308px}
.footer-col h4{color:#fff;font-size:18px;margin-bottom:14px}
.footer-col{font-size:11px;line-height:20px}
.col-links{width:190px}
.col-contact{width:230px;border-left:1px solid #3d4043;padding-left:24px}
.col-news{width:360px;border-left:1px solid #3d4043;padding-left:24px}
.col-follow{flex:1;border-left:1px solid #3d4043;padding-left:24px}
.contact-line{display:flex;align-items:center;gap:8px}
.news-field{width:300px;height:32px;background:#fff;margin-top:12px;display:flex;align-items:center;justify-content:space-between;padding:0 4px 0 10px;color:#999;border-radius:2px}
.news-field b{background:var(--blue);color:#fff;font-size:10px;padding:4px 10px;border-radius:2px}
.news-cta{margin-top:16px;display:flex;align-items:center;gap:16px}
.follow-item{display:flex;align-items:center;gap:10px;margin-bottom:4px}
.follow-item i{width:14px;height:14px;border-radius:50%;background:var(--orange);display:inline-block}
.footer-bottom{height:44px;background:var(--footer-bottom);font-size:10px;color:#8c9094}
.footer-bottom .container{display:flex;justify-content:space-between;align-items:center;height:44px;padding:0}
</style>
</head>
<body>

<div class="topbar">
  <div class="container">
    <div class="opts"><span>USD $ ▾</span><span>English ▾</span></div>
    <div class="account"><i></i><span>Sign In</span><span>|</span><span>Log in / Register</span></div>
  </div>
</div>

<header class="site-header">
  <div class="container">
    <div class="logo"><i></i>Caldera Key</div>
    <nav class="main-nav">
      <a class="active" href="#">Home</a>
      <a href="#">About Us</a>
      <a href="#">Holiday Packages</a>
      <a href="#">Services</a>
      <a href="#">Contacts</a>
    </nav>
  </div>
</header>

<section class="hero">
  <div class="hero-photo" role="img" aria-label="Tropical beach with a leaning palm tree, turquoise sea and white sand under a bright blue sky"></div>
  <div class="hero-copy">
    <h1>Let the activities begin!</h1>
    <div class="hero-search"><span>Search for your Tour</span><b>Let's Go!</b></div>
    <div class="hero-arrows">
      <span><svg width="8" height="10"><path d="M7 0L1 5l6 5z" fill="#333"/></svg></span>
      <span><svg width="8" height="10"><path d="M1 0l6 5-6 5z" fill="#333"/></svg></span>
    </div>
  </div>
  <svg class="hero-curve" width="1200" height="90" viewBox="0 0 1200 90"><path d="M0 0 Q600 110 1200 0 L1200 90 L0 90 Z" fill="#fff"/></svg>
</section>

<section class="welcome">
  <h2>Welcome to Caldera Key</h2>
  <p>Caldera Key gathers the best tours, stays and rides in our small mountain town. Browse local listings, read fresh news and plan every day of your trip with trusted guides who know each trail, river and café by name and heart.</p>
</section>

<section class="services">
  <div class="container">
    <article class="service">
      <div class="service-head"><h3>Selling guided tours</h3></div>
      <div class="service-icon">
        <svg width="90" height="60" viewBox="0 0 90 60" fill="#333"><circle cx="25" cy="14" r="9"/><circle cx="65" cy="14" r="9"/><circle cx="45" cy="20" r="8"/><path d="M10 58c0-18 7-30 15-30s15 12 15 30z"/><path d="M50 58c0-18 7-30 15-30s15 12 15 30z"/><path d="M33 58c0-16 5-26 12-26s12 10 12 26z" fill="#555"/></svg>
      </div>
      <p>Explore hidden trails with local guides who share stories, tips and the best views of the valley each morning.</p>
      <span class="btn">Read more</span>
    </article>
    <article class="service">
      <div class="service-head"><h3>Hotel/Hostels</h3></div>
      <div class="service-icon">
        <svg width="90" height="60" viewBox="0 0 90 60" fill="none" stroke="#333" stroke-width="4"><path d="M6 58V18M84 58V36M6 40h78M6 36h78"/><rect x="12" y="24" width="18" height="10" rx="4" fill="#333"/><path d="M34 34V26h46v10"/></svg>
      </div>
      <p>Find cozy hostels and family hotels close to the square, with fair rates and friendly hosts ready to help you.</p>
      <span class="btn">Read more</span>
    </article>
    <article class="service">
      <div class="service-head"><h3>Rental vehicles</h3></div>
      <div class="service-icon">
        <svg width="90" height="60" viewBox="0 0 90 60" fill="#333"><path d="M6 44V32l8-4 10-14h40l10 14 10 4v12z"/><path d="M28 18h15v10H21zM47 18h15l6 10H47z" fill="#fff"/><circle cx="24" cy="46" r="8" fill="#fff" stroke="#333" stroke-width="4"/><circle cx="66" cy="46" r="8" fill="#fff" stroke="#333" stroke-width="4"/></svg>
      </div>
      <p>Rent a car, scooter or jeep for the day and reach waterfalls, farms and lookouts at your own steady pace.</p>
      <span class="btn">Read more</span>
    </article>
  </div>
</section>

<section class="find">
  <div class="container">
    <h2>Caldera Key find holiday</h2>
    <p>Choose where you leave from, where you want to go and your dates. We compare small local operators so you can book a full holiday in minutes, with clear prices and friendly support from people who live here.</p>
    <div class="find-form">
      <span>Leaving from</span>
      <span>Going to</span>
      <span>Depart</span>
      <span>Return</span>
      <b class="btn">Find holiday</b>
    </div>
  </div>
</section>

<section class="packages">
  <div class="container">
    <h2>Be targeting tourism in a small town</h2>
    <div class="package-list">
      <article class="package">
        <div class="package-photo" role="img" aria-label="Limestone cliffs above a calm turquoise bay with boats" style="background:linear-gradient(180deg,#7fb7d9,#3f8d7a 55%,#2a9fb0)"></div>
        <div class="package-body">
          <h4>Majority have suffered</h4>
          <div class="rating"><span class="stars">★★★★☆</span><span>121 Reviews</span></div>
          <div class="place">Valley tour</div>
          <div class="package-foot"><div class="price"><small>From USD</small><b>$550.12</b></div><span class="btn">Book now</span></div>
        </div>
      </article>
      <article class="package">
        <div class="package-photo" role="img" aria-label="Palm trees leaning over a sandy shore and blue water" style="background:linear-gradient(180deg,#9fd0ec,#4fb6cf 50%,#3e7d4a 75%,#d8cfae)"></div>
        <div class="package-body">
          <h4>Majority have suffered</h4>
          <div class="rating"><span class="stars">★★★★☆</span><span>121 Reviews</span></div>
          <div class="place">Valley tour</div>
          <div class="package-foot"><div class="price"><small>From USD</small><b>$550.12</b></div><span class="btn">Book now</span></div>
        </div>
      </article>
      <article class="package">
        <div class="package-photo" role="img" aria-label="Green islet with a thatched hut surrounded by clear shallow sea" style="background:linear-gradient(180deg,#b5dcf0,#5bc3d3 45%,#3a8c5c 70%,#45b7c6)"></div>
        <div class="package-body">
          <h4>Majority have suffered</h4>
          <div class="rating"><span class="stars">★★★★☆</span><span>121 Reviews</span></div>
          <div class="place">Valley tour</div>
          <div class="package-foot"><div class="price"><small>From USD</small><b>$550.12</b></div><span class="btn">Book now</span></div>
        </div>
      </article>
      <article class="package">
        <div class="package-photo" role="img" aria-label="Ancient stone temple ruins covered by jungle trees" style="background:linear-gradient(180deg,#9bb88a,#5e7d46 45%,#7a6a4f 80%,#4e5a3a)"></div>
        <div class="package-body">
          <h4>Majority have suffered</h4>
          <div class="rating"><span class="stars">★★★★☆</span><span>121 Reviews</span></div>
          <div class="place">Valley tour</div>
          <div class="package-foot"><div class="price"><small>From USD</small><b>$550.12</b></div><span class="btn">Book now</span></div>
        </div>
      </article>
    </div>
  </div>
</section>

<footer class="site-footer">
  <div class="container">
    <div class="footer-col col-links">
      <h4>Caldera Key</h4>
      <div>Home</div><div>About US</div><div>Holiday Packages</div><div>Services</div><div>Contacts</div>
    </div>
    <div class="footer-col col-contact">
      <h4>Contact us</h4>
      <div>Caldera Key</div>
      <div>0400 Central Valley, Panama</div>
      <div class="contact-line"><svg width="12" height="9"><rect x=".5" y=".5" width="11" height="8" fill="none" stroke="#f07b2b"/><path d="M.5 .5l5.5 4 5.5-4" fill="none" stroke="#f07b2b"/></svg>info@calderakey.example</div>
      <div class="contact-line"><svg width="12" height="12"><path d="M2 1l3 0 1 3-2 1c1 2 2 3 4 4l1-2 3 1v3c-6 0-10-4-10-10z" fill="#f07b2b"/></svg>+00 555 010 2231</div>
      <div class="contact-line"><svg width="12" height="12"><path d="M2 1l3 0 1 3-2 1c1 2 2 3 4 4l1-2 3 1v3c-6 0-10-4-10-10z" fill="#f07b2b"/></svg>+00 555 010 2232</div>
    </div>
    <div class="footer-col col-news">
      <h4>Sign to newsletter</h4>
      <div>Join our local newsletter for the latest offers, events and news from town.</div>
      <div class="news-field"><span>Name</span><b>Submit</b></div>
      <div class="news-cta">
        <svg width="40" height="30" viewBox="0 0 40 30"><path d="M4 28A16 16 0 0 1 36 28" fill="none" stroke="#1f78ad" stroke-width="6"/></svg>
        <span class="btn">Call to act</span>
      </div>
    </div>
    <div class="footer-col col-follow">
      <h4>Follow us</h4>
      <div class="follow-item"><i></i>Chatterly</div>
      <div class="follow-item"><i></i>Tweetline</div>
      <div class="follow-item"><i></i>Vidcast</div>
      <div class="follow-item"><i></i>Snapgrid</div>
    </div>
  </div>
  <div class="footer-bottom">
    <div class="container"><span>Caldera Key © 2015. All rights reserved.</span><span>1 / 6</span></div>
  </div>
</footer>

</body>
</html>
```